Brookmere Osteopathy flyer

I want a clean clear DL flyer (but also want an A4 poster) promoting a new Osteopathic business in a semi rural area in Tasmania (Australia).
It can have pictures like the examples attached to show people what Osteopathy is (its like Chiropractic and physiotherapy).
I am the sole practioner and am male, so any pictures would be best to be a white male if possible.
I've attached some wording, you can use all, or none of it
I don't have a phone number for the business yet
info@brookmereosteopathy.example
www.brookmereosteopathy.example
Target Market(s)
Australians, from tradies, professionals, babies to retired people
Industry/Entity Type
Health
Look and feel

```html
<!DOCTYPE html>
<html lang="en">
<head>
<meta charset="utf-8">
<title>Brookmere Osteopathy flyers</title>
<link rel="stylesheet" href="https://fonts.googleapis.com/css2?family=Open+Sans:wght@400;600;700;800&display=swap">
<style>
:root{
  --navy:#0b0f5c;
  --navy-deep:#070a3f;
  --brand-blue:#0a8ed6;
  --heading-blue:#0a86cf;
  --stripe:#2b2fa0;
  --accent-light:#5cbcf0;
  --ink:#1a1a1a;
  --white:#ffffff;
  --page:#ffffff;
}
*{margin:0;padding:0;box-sizing:border-box}
html,body{width:1200px;height:848px;overflow:hidden;background:var(--page)}
body{position:relative;font-family:"Open Sans",Arial,sans-serif;color:var(--ink)}
.flyer{position:absolute;top:49px;height:751px;background:var(--white);overflow:hidden;box-shadow:0 0 2px rgba(0,0,0,.25)}
.flyer--dl{left:147px;width:354px}
.flyer--a4{left:524px;width:532px}
.flyer > *{position:absolute}
.shapes{left:0;top:0;width:100%;height:100%}
.portrait{background:linear-gradient(160deg,#c9cfd8 0%,#eef1f5 45%,#b9c3d4 100%);border-radius:0 0 4px 4px;z-index:1}
.brand{display:flex;flex-direction:column;align-items:center;gap:4px;text-align:center;color:var(--white);font-weight:700;z-index:2}
.brand__dot{width:18px;height:18px;border-radius:50%;border:2px solid var(--accent-light);flex:none}
.headline{color:var(--white);font-weight:800;letter-spacing:-.2px;white-space:nowrap;z-index:2}
.headline span{display:block}
.headline .headline__accent{color:var(--accent-light)}
.section-title{color:var(--heading-blue);font-weight:800;white-space:nowrap}
.body-copy{color:var(--ink);font-weight:400}
.photo{border-radius:8px}
.photo--back{background:linear-gradient(135deg,#e9c6a6,#c99774)}
.photo--baby{background:linear-gradient(160deg,#e8c8b2 0%,#d8b39a 50%,#3d8fc4 100%)}
.photo--neck{background:linear-gradient(150deg,#f1f1f1 0%,#d9a988 55%,#2a3b4b 100%)}
.photo--abdomen{background:linear-gradient(135deg,#f3e4d8,#d5a98a)}
.assist-title{color:var(--heading-blue);font-weight:800;white-space:nowrap}
.assist-list{list-style:none;border-left:1.2px solid var(--brand-blue);white-space:nowrap}
.assist-list li{position:relative}
.assist-list li::before{content:"";position:absolute;left:-3.5px;top:50%;width:6px;height:6px;margin-top:-3px;border-radius:50%;background:var(--brand-blue)}
.flyer--dl .assist-list li{padding-left:6px}
.flyer--a4 .assist-list li{padding-left:8px}
.flyer--dl .assist-list li::before{left:-3.5px}
.contact-title{color:var(--white);font-weight:800;text-align:center}
.contact-list{list-style:none;color:var(--white)}
.contact-list li{display:flex;align-items:center;white-space:nowrap}
.contact-list svg{flex:none}
.contact-list .spaced{letter-spacing:var(--track)}

/* DL sizing */
.flyer--dl .brand{left:14px;top:30px;width:92px;font-size:11px;line-height:13px}
.flyer--dl .portrait{left:182px;top:12px;width:164px;height:255px}
.flyer--dl .headline{left:17px;top:108px;font-size:22.5px;line-height:23px}
.flyer--dl .title-what{left:21px;top:296px;font-size:23px}
.flyer--dl .copy-what{left:21px;top:330px;width:312px;font-size:14.2px;line-height:16.7px}
.flyer--dl .assist-title{left:188px;top:397px;font-size:14.5px;line-height:17px}
.flyer--dl .assist-list{left:185px;top:434px;font-size:13.4px;line-height:15.6px}
.flyer--dl .title-who{left:21px;top:538px;font-size:23px}
.flyer--dl .copy-who{left:21px;top:574px;width:306px;font-size:14.2px;line-height:16.7px}
.flyer--dl .contact-title{left:0;width:350px;top:659px;font-size:14px}
.flyer--dl .contact-list{left:45px;top:690px;font-size:12px;line-height:15px;--track:1.1px}
.flyer--dl .contact-list svg{margin-right:5px}

/* A4 sizing */
.flyer--a4 .brand{left:14px;top:100px;width:86px;font-size:11px;line-height:13px}
.flyer--a4 .portrait{left:312px;top:12px;width:166px;height:240px}
.flyer--a4 .headline{left:111px;top:44px;font-size:29px;line-height:29px}
.flyer--a4 .title-what{left:38px;top:270px;font-size:21px}
.flyer--a4 .copy-what{left:38px;top:300px;width:480px;font-size:13px;line-height:15.3px}
.flyer--a4 .assist-title{left:271px;top:352px;font-size:19px;line-height:22.5px}
.flyer--a4 .assist-list{left:270px;top:405px;font-size:17px;line-height:21.4px}
.flyer--a4 .title-who{left:38px;top:534px;font-size:21px}
.flyer--a4 .copy-who{left:38px;top:564px;width:480px;font-size:13px;line-height:15.3px}
.flyer--a4 .contact-title{left:0;width:528px;top:627px;font-size:17px}
.flyer--a4 .contact-list{left:102px;top:667px;font-size:15px;line-height:19px;--track:1.5px}
.flyer--a4 .contact-list svg{margin-right:6px}
</style>
</head>
<body>

<section class="flyer flyer--dl" aria-label="Brookmere Osteopathy DL flyer">
  <svg class="shapes" viewBox="0 0 354 751" aria-hidden="true">
    <defs>
      <linearGradient id="dl-header" x1="0" y1="0" x2="1" y2="1">
        <stop offset="0" stop-color="#0d1a8a"/>
        <stop offset=".6" stop-color="#0b0f5c"/>
        <stop offset="1" stop-color="#070a3f"/>
      </linearGradient>
    </defs>
    <polygon points="25,214 172,270 325,220 325,236 172,284 25,228" fill="var(--brand-blue)"/>
    <polygon points="0,0 354,0 354,207 172,272 0,216" fill="url(#dl-header)"/>
    <polygon points="30,688 177,637 331,690 331,697 177,645 30,695" fill="var(--stripe)"/>
    <polygon points="0,707 177,646 354,707 354,751 0,751" fill="var(--brand-blue)"/>
  </svg>
  <div class="portrait" role="img" aria-label="Photo of the osteopath in a white coat, arms folded"></div>

  <div class="brand"><span class="brand__dot"></span><span>Brookmere<br>Osteopathy</span></div>

  <h1 class="headline"><span>This isn't just</span><span>treatment.</span><span>This is your</span><span class="headline__accent">life again.</span></h1>

  <h2 class="section-title title-what">What is Osteopathy?</h2>
  <p class="body-copy copy-what">Gentle treatment to reduce pain, improve mobility and help your body heal naturally using massage, joint movement &amp; stretching.</p>

  <div class="photo photo--back" role="img" aria-label="Practitioner treating a patient's shoulder" style="left:16px;top:382px;width:73px;height:68px"></div>
  <div class="photo photo--baby" role="img" aria-label="Gentle head treatment of a newborn" style="left:94px;top:382px;width:74px;height:68px"></div>
  <div class="photo photo--neck" role="img" aria-label="Practitioner treating a woman's neck" style="left:16px;top:455px;width:73px;height:68px"></div>
  <div class="photo photo--abdomen" role="img" aria-label="Hands-on abdominal treatment" style="left:94px;top:455px;width:74px;height:68px"></div>

  <h3 class="assist-title">Osteopathy can<br>assist with:</h3>
  <ul class="assist-list">
    <li>Back &amp; neck pain</li>
    <li>Sciatica &amp; disc issues</li>
    <li>Headaches</li>
    <li>Pregnancy discomfort</li>
    <li>Joint &amp; muscle problems</li>
  </ul>

  <h2 class="section-title title-who">Who Do We Treat?</h2>
  <p class="body-copy copy-who">From active tradies and busy professionals to newborns and retirees — everyone is welcome. Treatments are always adjusted to suit your body, your lifestyle, and your goals.</p>

  <h3 class="contact-title">Contact Us:</h3>
  <ul class="contact-list">
    <li><svg width="10" height="8" viewBox="0 0 10 8"><rect x=".5" y=".5" width="9" height="7" fill="none" stroke="#fff"/><path d="M.5 .5 5 4.5 9.5 .5" fill="none" stroke="#fff"/></svg><span class="spaced">info@brookmereosteopathy.example</span></li>
    <li><svg width="10" height="10" viewBox="0 0 10 10"><circle cx="5" cy="5" r="4.3" fill="none" stroke="#fff"/><ellipse cx="5" cy="5" rx="2" ry="4.3" fill="none" stroke="#fff"/><path d="M.7 5h8.6" stroke="#fff"/></svg><span class="spaced">www.brookmereosteopathy.example</span></li>
    <li><svg width="10" height="11" viewBox="0 0 10 11"><path d="M5 10.5S1 6.3 1 4a4 4 0 0 1 8 0c0 2.3-4 6.5-4 6.5z" fill="#fff"/><circle cx="5" cy="4" r="1.5" fill="var(--brand-blue)"/></svg><span>Serving Brookmere and surrounding areas</span></li>
  </ul>
</section>

<section class="flyer flyer--a4" aria-label="Brookmere Osteopathy A4 poster">
  <svg class="shapes" viewBox="0 0 532 751" aria-hidden="true">
    <defs>
      <linearGradient id="a4-header" x1="0" y1="0" x2="1" y2="1">
        <stop offset="0" stop-color="#0d1a8a"/>
        <stop offset=".6" stop-color="#0b0f5c"/>
        <stop offset="1" stop-color="#070a3f"/>
      </linearGradient>
    </defs>
    <polygon points="81,187 267,250 460,181 460,201 267,265 81,200" fill="var(--brand-blue)"/>
    <polygon points="0,0 532,0 532,154 267,253 0,160" fill="url(#a4-header)"/>
    <polygon points="79,665 265,603 459,673 459,680 265,612 79,672" fill="var(--stripe)"/>
    <polygon points="0,697 265,612 532,705 532,751 0,751" fill="var(--brand-blue)"/>
  </svg>
  <div class="portrait" role="img" aria-label="Photo of the osteopath in a white coat"></div>

  <div class="brand"><span class="brand__dot"></span><span>Brookmere<br>Osteopathy</span></div>

  <h1 class="headline"><span>This isn't just</span><span>treatment.</span><span>This is your</span><span class="headline__accent">life again.</span></h1>

  <h2 class="section-title title-what">What is Osteopathy?</h2>
  <p class="body-copy copy-what">Gentle treatment to reduce pain, improve mobility and help your body heal naturally using massage, joint movement &amp; stretching.</p>

  <div class="photo photo--back" role="img" aria-label="Practitioner treating a patient's shoulder" style="left:41px;top:342px;width:96px;height:88px"></div>
  <div class="photo photo--baby" role="img" aria-label="Gentle head treatment of a newborn" style="left:141px;top:342px;width:95px;height:88px"></div>
  <div class="photo photo--neck" role="img" aria-label="Practitioner treating a woman's neck" style="left:41px;top:437px;width:96px;height:87px"></div>
  <div class="photo photo--abdomen" role="img" aria-label="Hands-on abdominal treatment" style="left:141px;top:437px;width:95px;height:87px"></div>

  <h3 class="assist-title">Osteopathy can<br>assist with:</h3>
  <ul class="assist-list">
    <li>Back &amp; neck pain</li>
    <li>Sciatica &amp; disc issues</li>
    <li>Headaches</li>
    <li>Pregnancy discomfort</li>
    <li>Joint &amp; muscle problems</li>
  </ul>

  <h2 class="section-title title-who">Who Do We Treat?</h2>
  <p class="body-copy copy-who">From active tradies and busy professionals to newborns and retirees — everyone is welcome. Treatments are always adjusted to suit your body, your lifestyle, and your goals.</p>

  <h3 class="contact-title">Contact Us:</h3>
  <ul class="contact-list">
    <li><svg width="12" height="9" viewBox="0 0 12 9"><rect x=".5" y=".5" width="11" height="8" fill="none" stroke="#fff"/><path d="M.5 .5 6 5 11.5 .5" fill="none" stroke="#fff"/></svg><span class="spaced">info@brookmereosteopathy.example</span></li>
    <li><svg width="12" height="12" viewBox="0 0 12 12"><circle cx="6" cy="6" r="5.3" fill="none" stroke="#fff"/><ellipse cx="6" cy="6" rx="2.4" ry="5.3" fill="none" stroke="#fff"/><path d="M.7 6h10.6" stroke="#fff"/></svg><span class="spaced">www.brookmereosteopathy.example</span></li>
    <li><svg width="12" height="13" viewBox="0 0 12 13"><path d="M6 12.5S1 7.5 1 4.8a5 5 0 0 1 10 0C11 7.5 6 12.5 6 12.5z" fill="#fff"/><circle cx="6" cy="4.8" r="1.8" fill="var(--brand-blue)"/></svg><span>Serving Brookmere and surrounding areas</span></li>
  </ul>
</section>

</body>
</html>
```